Building technology company seek stationery design and folder design

Letterhead, and a folder design
ideally, I would have two letter head design, one is for one-page bussiness letter. the other one I can use for longer document such report, or analysis regular report page
you can find company logo and overall style at our website:
www.structavolt.example

we are in building technology business, using internet of things technology to improve building energy efficiency to make building greener.

Industry/Entity Type

It Company

Requirements
Must have
• company logo
Nice to have
• techy look abstract graphics, etc.
Should not have
• no comment

```html
<!DOCTYPE html>
<html lang="en">
<head>
<meta charset="utf-8">
<title>Structavolt Stationery</title>
<link href="https://fonts.googleapis.com/css2?family=Questrial&display=swap" rel="stylesheet">
<style>
  :root {
    --bg: #dedede;
    --paper: #ffffff;
    --paper-shade: #eeeeee;
    --green: #b1d34b;
    --green-deep: #9cc23a;
    --green-light: #c9e479;
    --text: #4a4a4a;
    --text-soft: #6b6b6b;
    --circuit-grey: #d9d9d9;
  }
  * { margin: 0; padding: 0; box-sizing: border-box; }
  html, body { width: 1200px; height: 821px; overflow: hidden; }
  body {
    background: var(--bg);
    font-family: "Questrial", "Century Gothic", sans-serif;
    color: var(--text);
    position: relative;
  }

  /* Letterhead */
  .letterhead {
    position: absolute;
    left: 74px; top: 114px;
    width: 441px; height: 620px;
    background: linear-gradient(90deg, var(--paper) 0%, var(--paper-shade) 100%);
    overflow: hidden;
  }
  .letterhead .circuit {
    position: absolute; left: 0; top: 250px; width: 441px; height: 362px;
    background:
      linear-gradient(180deg, rgba(217,217,217,0) 0%, rgba(217,217,217,0.55) 40%, var(--circuit-grey) 100%),
      linear-gradient(90deg, rgba(217,217,217,0.25) 0%, rgba(217,217,217,0) 40%, rgba(217,217,217,0.5) 100%);
  }
  .letterhead .brand {
    position: absolute; left: 38px; top: 76px;
    display: flex; align-items: center; gap: 5px;
  }
  .letterhead .brand-mark { width: 9px; height: 9px; background: var(--green); }
  .letterhead .brand-name {
    font-size: 11px; letter-spacing: 0.6px; color: var(--green-deep);
    text-transform: uppercase; line-height: 1;
  }
  .contact {
    position: absolute; left: 315px; top: 49px;
    list-style: none; font-size: 6.6px; color: var(--text-soft); line-height: 9px;
  }
  .contact li { display: flex; align-items: center; gap: 4px; }
  .contact svg { width: 6px; height: 6px; fill: var(--green); flex: none; }
  .letter {
    position: absolute; left: 40px; top: 173px; width: 366px;
  }
  .salutation { font-size: 11.5px; color: var(--text); margin-bottom: 17px; line-height: 14px; }
  .letter p.body-copy {
    font-size: 6.3px; line-height: 9.6px; color: var(--text-soft);
    margin-bottom: 9.6px; text-align: justify;
  }
  .closing {
    position: absolute; left: 40px; top: 408px;
    font-size: 6.3px; color: var(--text-soft);
  }
  .signature {
    position: absolute; left: 36px; top: 434px; width: 80px; height: 30px;
    background: linear-gradient(90deg, rgba(177,211,75,0.35), rgba(177,211,75,0.1));
    border-radius: 3px;
  }
  .letterhead .footer-rule {
    position: absolute; left: 0; bottom: 7px; width: 100%; height: 1px; background: #8a9a5a;
  }
  .letterhead .footer-band {
    position: absolute; left: 0; bottom: 0; width: 100%; height: 7px; background: var(--green);
  }

  /* Folder */
  .folder {
    position: absolute;
    left: 553px; top: 77px;
    width: 520px; height: 657px;
    background: var(--green);
    overflow: hidden;
  }
  .folder .circuit {
    position: absolute; left: 0; top: 180px; width: 100%; height: 471px;
    background:
      radial-gradient(circle at 65% 30%, rgba(255,255,255,0.18), transparent 45%),
      linear-gradient(180deg, rgba(201,228,121,0) 0%, rgba(201,228,121,0.7) 45%, var(--green-light) 100%);
  }
  .folder .spine {
    position: absolute; top: 0; width: 1px; height: 651px; background: rgba(255,255,255,0.3);
  }
  .folder .brand {
    position: absolute; left: 0; top: 152px; width: 100%;
    display: flex; justify-content: center; align-items: center; gap: 12px;
  }
  .folder .brand-mark { width: 22px; height: 22px; background: #ffffff; }
  .folder .brand-name {
    font-size: 30px; letter-spacing: 1.5px; color: #ffffff;
    text-transform: uppercase; line-height: 1;
  }
  .folder .base-strip {
    position: absolute; left: 0; bottom: 0; width: 100%; height: 6px; background: #ffffff;
  }
</style>
</head>
<body>

<section class="letterhead" aria-label="Letterhead">
  <div class="circuit" role="img" aria-label="Faint grey circuit-board line pattern"></div>

  <div class="brand">
    <span class="brand-mark"></span>
    <span class="brand-name">Structavolt</span>
  </div>

  <ul class="contact">
    <li>
      <svg viewBox="0 0 10 10"><path d="M2 1l2 0 1 2.5-1.2 1a6 6 0 0 0 2.7 2.7l1-1.2 2.5 1 0 2c-5 0.5-9-3.5-8.5-8z"/></svg>
      (555) 014-2290
    </li>
    <li>
      <svg viewBox="0 0 10 10"><rect x="0.5" y="2" width="9" height="6"/></svg>
      info@structavolt.example
    </li>
    <li>
      <svg viewBox="0 0 10 10"><circle cx="5" cy="5" r="4.5"/></svg>
      www.structavolt.example
    </li>
    <li>
      <svg viewBox="0 0 10 10"><circle cx="5" cy="5" r="4.5"/></svg>
      structavolt
    </li>
  </ul>

  <div class="letter">
    <p class="salutation">Dear Mr. Harlow,</p>
    <p class="body-copy">Thank you for meeting with our team last week to review the energy profile of your office tower. As discussed, our sensor network will monitor lighting, heating and cooling loads in real time and report savings to your facilities staff each month. We expect the first results within six weeks of installation and will share a summary with you and your board.</p>
    <p class="body-copy">Enclosed you will find the proposed schedule, the list of devices to be fitted on each floor and an outline of the dashboard your team will use. Please review the plan with your building manager and let us know of any areas that need special access, escorts or after-hours work during the fitting period.</p>
    <p class="body-copy">Our engineers will also carry out a short survey of the rooftop plant and the main electrical panels. This helps us place meters where they give the clearest picture of daily use. Once the system is live, alerts will be sent when equipment runs outside its normal range, so small faults can be fixed before they become costly repairs. We will train two members of your staff to read the reports and adjust settings.</p>
    <p class="body-copy">We look forward to helping your building use less energy and run more smoothly. Should you have any questions before we begin, please contact our office and we will be glad to assist.</p>
  </div>

  <p class="closing">Sincerely,</p>
  <div class="signature" role="img" aria-label="Handwritten signature of Dana Reyes"></div>

  <div class="footer-rule"></div>
  <div class="footer-band"></div>
</section>

<section class="folder" aria-label="Presentation folder cover">
  <div class="circuit" role="img" aria-label="Light green circuit-board line pattern with soft glowing dots"></div>
  <div class="spine" style="left:11px"></div>
  <div class="spine" style="left:17px"></div>
  <div class="spine" style="left:31px"></div>

  <div class="brand">
    <span class="brand-mark"></span>
    <span class="brand-name">Structavolt</span>
  </div>

  <div class="base-strip"></div>
</section>

</body>
</html>
```